W. Darrow Billboard

2 miles ahead on right
Voted number 1 ... again!
California cuisine
Located in Historic Marbury Hill Inn
Picture of a couple dining
www.torvellis.com 555.317.2968

Target Market(s)

travelers

Industry/Entity Type

hospitality

Font styles to use
Serif

Colors
59FF00
82FF00
B8FF75
E3FFCB
F4FFEA
EE7325
F08F49
F5BC92
FAE3D3
FDF4ED

Requirements
Should not have
• bright colors

```html
<!DOCTYPE html>
<html lang="en">
<head>
<meta charset="utf-8">
<title>W. Darrow Billboard</title>
<link rel="stylesheet" href="https://fonts.googleapis.com/css2?family=Signika:wght@400;600;700&family=Bree+Serif&display=swap">
<style>
  :root {
    --sky: #e9eef2;
    --cream: #f4ffea;
    --cream-deep: #e3ffcb;
    --leaf: #5aa51f;
    --leaf-dark: #3f8a14;
    --leaf-light: #8cc63f;
    --lime-tint: #b8ff75;
    --ink-grey: #6b6b6b;
    --orange: #ee7325;
    --orange-soft: #f08f49;
    --gold: #d9a531;
    --gold-deep: #a8731a;
    --photo-warm: #b7896a;
    --photo-cool: #6f8a7a;
    --photo-dark: #6b4a3a;
    --white: #ffffff;
  }
  * { box-sizing: border-box; margin: 0; padding: 0; }
  html, body { width: 1200px; height: 800px; overflow: hidden; }
  body { background: var(--sky); font-family: "Signika", sans-serif; position: relative; }

  .billboard {
    position: absolute; left: 20px; top: 140px; width: 1160px; height: 520px;
    background: linear-gradient(180deg, var(--white), var(--cream));
    overflow: hidden;
  }
  .shapes { position: absolute; inset: 0; }

  .tagline {
    position: absolute; left: 60px; top: 32px;
    font-family: "Bree Serif", serif; font-size: 46px; color: var(--white);
    transform: rotate(6deg); transform-origin: left center;
    letter-spacing: 1px;
  }
  .headline {
    position: absolute; left: 36px; top: 128px;
    font-family: "Signika", sans-serif; font-weight: 700; font-size: 84px;
    color: var(--leaf-light);
    -webkit-text-stroke: 3px var(--leaf-dark);
    letter-spacing: 1px;
  }
  .venue {
    position: absolute; left: 300px; top: 228px;
    font-family: "Signika", sans-serif; font-weight: 600; font-size: 32px;
    color: var(--ink-grey);
  }
  .award {
    position: absolute; left: 36px; top: 238px; width: 170px; height: 170px;
    border-radius: 50%;
    background: radial-gradient(circle at 50% 45%, var(--gold) 0%, var(--gold-deep) 70%, transparent 72%);
  }
  .contact {
    position: absolute; left: 24px; bottom: 26px;
    display: flex; gap: 380px;
    font-family: "Signika", sans-serif; font-weight: 700; font-size: 44px; color: var(--white);
  }
  .photo {
    position: absolute; width: 200px; height: 126px; border-radius: 28px;
    border: 4px solid #555;
  }
  .photo--terrace { left: 330px; top: 280px; background: linear-gradient(135deg, var(--photo-cool), var(--photo-warm)); }
  .photo--patio { left: 575px; top: 300px; background: linear-gradient(135deg, var(--photo-warm), var(--photo-cool)); }
  .photo--dining { left: 820px; top: 318px; background: linear-gradient(135deg, var(--photo-dark), var(--photo-warm)); }

  .brand {
    position: absolute; left: 700px; top: 110px; width: 430px;
    display: flex; align-items: center; gap: 16px;
    font-family: "Signika", sans-serif; font-weight: 700; color: var(--orange);
  }
  .brand__mark { width: 40px; height: 40px; border-radius: 50%; background: var(--leaf-light); flex: none; }
  .brand__name { font-size: 42px; line-height: 1.05; }
</style>
</head>
<body>
  <main class="billboard">
    <svg class="shapes" width="1160" height="520" viewBox="0 0 1160 520" aria-hidden="true">
      <defs>
        <linearGradient id="bandFade" x1="0" y1="0" x2="1" y2="0">
          <stop offset="0" stop-color="#5aa51f"/>
          <stop offset="0.7" stop-color="#6fb52c"/>
          <stop offset="1" stop-color="#6fb52c" stop-opacity="0"/>
        </linearGradient>
      </defs>
      <!-- lower band -->
      <rect x="0" y="410" width="1160" height="110" fill="url(#bandFade)"/>
      <!-- ribbon banner -->
      <path d="M0 0 H300 C420 10 500 60 560 110 L600 150 L540 140 L500 160 C430 120 340 110 0 112 Z" fill="#4e9a1c"/>
      <path d="M0 0 H300 C360 4 400 18 430 34 C330 20 200 20 0 24 Z" fill="#8cc63f"/>
      <!-- logo area curve -->
      <path d="M640 20 C560 120 640 300 1160 330" fill="none" stroke="#6fb52c" stroke-width="8"/>
    </svg>

    <p class="tagline">Good Food, Good Life</p>
    <h1 class="headline">California Cuisine</h1>
    <p class="venue">Historic Marbury Hill Inn</p>

    <div class="award" role="img" aria-label="Gold trophy award badge reading Voted No. 1 again"></div>

    <div class="photo photo--terrace" role="img" aria-label="Photo of a couple dining on a terrace"></div>
    <div class="photo photo--patio" role="img" aria-label="Photo of a couple sharing dishes on a patio"></div>
    <div class="photo photo--dining" role="img" aria-label="Photo of a couple at a candlelit dining room table"></div>

    <div class="brand">
      <span class="brand__mark"></span>
      <span class="brand__name">Torvelli's Southwest Bar &amp; Grill</span>
    </div>

    <div class="contact">
      <span class="contact__phone">555.317.2968</span>
      <span class="contact__web">www.torvellis.com</span>
    </div>
  </main>
</body>
</html>
```